Business Card Design

We need the business card for our new business based in St. Marys, we manufacture mainly bubble wraps. And we would like the design to use our company logo and also make it easy for people to understand right away we are bubble wrap manufacturer

Industry/Entity Type

Business

Contact Information for Business Card

Cushtane Pty Ltd, 14 Larkin Road Harlow Vale NSW 2791, Tel: 02 9471 5826, Fax: 9471 5839, Dara Oyelaran, General Manager, Mobile :0438 217 564, dara.oyelaran@cushtane.com.au, Website: cushtane.com.au

```html
<!DOCTYPE html>
<html lang="en">
<head>
<meta charset="utf-8">
<title>Cushtane Pty Ltd — Business Card</title>
<link rel="stylesheet" href="https://fonts.googleapis.com/css2?family=Montserrat:wght@400;500;700;800&display=swap">
<style>
  :root {
    --backdrop: #e4e4e4;
    --card-black: #0e0e0f;
    --card-white: #ffffff;
    --brand-grey: #5f5f5f;
    --tagline-grey: #7d7d7d;
    --band-grey: #6e6e6e;
    --brand-red: #b3241f;
    --ink-white: #ffffff;
  }
  * { box-sizing: border-box; margin: 0; padding: 0; }
  html, body {
    width: 1200px; height: 852px; overflow: hidden;
    background: var(--backdrop);
    font-family: "Montserrat", Arial, sans-serif;
  }
  .stage { position: relative; width: 1200px; height: 852px; }

  .card {
    position: absolute;
    width: 600px; height: 343px;
    border-radius: 12px;
    overflow: hidden;
    box-shadow: 0 6px 18px rgba(0,0,0,0.18);
  }
  .card--front { left: 150px; top: 70px; background: var(--card-black); }
  .card--back  { left: 450px; top: 440px; background: var(--card-white); }

  .wordmark {
    position: absolute;
    display: flex; flex-direction: column; align-items: flex-start;
  }
  .wordmark__name {
    font-weight: 800;
    font-size: 64px;
    letter-spacing: 1px;
    line-height: 1;
    color: var(--brand-grey);
  }
  .wordmark__tagline {
    margin-top: 10px;
    font-weight: 500;
    font-size: 14.5px;
    letter-spacing: 5.2px;
    color: var(--tagline-grey);
    white-space: nowrap;
  }
  .card--front .wordmark { left: 78px; top: 118px; }
  .card--front .wordmark__name { color: #6a6a6a; }
  .card--front .wordmark__tagline { color: #4e4e4e; }
  .card--back .wordmark { left: 78px; top: 58px; }

  .card__band {
    position: absolute; left: 0; right: 0;
    top: 180px; height: 8px;
    background: var(--band-grey);
  }
  .card__panel {
    position: absolute; left: 0; right: 0;
    top: 188px; bottom: 0;
    background: var(--brand-red);
    color: var(--ink-white);
  }
  .person {
    position: absolute; left: 32px; top: 66px;
  }
  .person__name {
    font-weight: 700; font-size: 16px; letter-spacing: 0.5px;
    text-transform: uppercase;
  }
  .person__role { font-weight: 400; font-size: 13px; margin-top: 2px; }

  .contact {
    position: absolute; left: 300px; top: 14px;
    list-style: none;
    font-size: 13px; font-weight: 400; line-height: 19px;
  }
  .contact__address { margin-bottom: 1px; white-space: nowrap; }
  .contact__item { display: flex; align-items: center; gap: 9px; white-space: nowrap; }
  .contact__icon { width: 12px; height: 12px; flex: none; fill: var(--ink-white); }
</style>
</head>
<body>
<main class="stage">

  <section class="card card--front" aria-label="Card front">
    <div class="wordmark">
      <span class="wordmark__name">CUSHTANE</span>
      <span class="wordmark__tagline">PROTECTIVE PACKAGING SOLUTIONS</span>
    </div>
  </section>

  <section class="card card--back" aria-label="Card back">
    <div class="wordmark">
      <span class="wordmark__name">CUSHTANE</span>
      <span class="wordmark__tagline">PROTECTIVE PACKAGING SOLUTIONS</span>
    </div>
    <div class="card__band"></div>
    <div class="card__panel">
      <div class="person">
        <p class="person__name">Dara Oyelaran</p>
        <p class="person__role">General Manager</p>
      </div>
      <ul class="contact">
        <li class="contact__address">14 Larkin Road Harlow Vale NSW 2791</li>
        <li class="contact__item">
          <svg class="contact__icon" viewBox="0 0 12 12" aria-hidden="true"><path d="M1 4c0-2 1-3 5-3s5 1 5 3l-2 1-1-2H4L3 5zM3 6h6l1 5H2z"/></svg>
          <span>02 9471 5826</span>
        </li>
        <li class="contact__item">
          <svg class="contact__icon" viewBox="0 0 12 12" aria-hidden="true"><path d="M3 0h6v4H3zM1 5h10v7H1z"/><rect x="3" y="7" width="6" height="1.2" fill="#b3241f"/><rect x="3" y="9" width="6" height="1.2" fill="#b3241f"/></svg>
          <span>9471 5839</span>
        </li>
        <li class="contact__item">
          <svg class="contact__icon" viewBox="0 0 12 12" aria-hidden="true"><path d="M3 0h6a1 1 0 0 1 1 1v10a1 1 0 0 1-1 1H3a1 1 0 0 1-1-1V1a1 1 0 0 1 1-1z"/><rect x="3.5" y="1.5" width="5" height="7" fill="#b3241f"/></svg>
          <span>0438 217 564</span>
        </li>
        <li class="contact__item">
          <svg class="contact__icon" viewBox="0 0 12 12" aria-hidden="true"><path d="M0 2h12v8H0z"/><path d="M0 2l6 5 6-5" fill="none" stroke="#b3241f" stroke-width="1.2"/></svg>
          <span>dara.oyelaran@cushtane.com.au</span>
        </li>
        <li class="contact__item">
          <svg class="contact__icon" viewBox="0 0 12 12" aria-hidden="true"><circle cx="6" cy="6" r="6"/><path d="M0 6h12M6 0v12M6 0c-3 3-3 9 0 12M6 0c3 3 3 9 0 12" fill="none" stroke="#b3241f" stroke-width="0.9"/></svg>
          <span>www.cushtane.com.au</span>
        </li>
      </ul>
    </div>
  </section>

</main>
</body>
</html>
```